Dusty Spur Outfitters Home Page

I need a logo and page design for my home page, maybe some background color suggestions to go with it. I want the logo to project "vintage" and "western wear" but not be your typical trite western saddle and gun type thing.
http://www.dustyspuroutfitters.example/store/cart.php
Not looking for page coding just logo and other design elements to lay in over the site's template to make it "pop"
Reason: Have to finalize the design.
Target Market(s)
My customers are 70/30 men to women.
Industry/Entity Type
Gun

```html
<!DOCTYPE html>
<html lang="en">
<head>
<meta charset="utf-8">
<title>Dusty Spur Outfitters</title>
<link href="https://fonts.googleapis.com/css2?family=Rye&family=Lato:wght@400;700&display=swap" rel="stylesheet">
<style>
:root{
  --dark:#333333;
  --sand:#e0d6c0;
  --tan:#c5b99e;
  --teal:#3a9fb0;
  --ink:#2b2b2b;
  --cream:#efe6d2;
}
*{margin:0;padding:0;box-sizing:border-box}
html,body{width:1200px;height:904px;overflow:hidden}
body{background:var(--sand);font-family:'Lato',sans-serif;color:var(--ink);position:relative}
.abs{position:absolute}
.topbar{left:0;top:0;width:1200px;height:28px;background:var(--dark)}
.topnav{left:38px;top:8px;font-size:11px;font-weight:700;color:var(--sand);letter-spacing:.1px;display:flex;gap:9px}
.helpnav{left:543px;top:8px;font-size:11px;font-weight:700;color:var(--sand);display:flex;gap:9px}
.account-icons{left:1098px;top:6px}
.header{left:0;top:35px;width:1200px;height:110px;background:var(--dark)}
.brand{left:41px;top:60px;font-family:'Rye',serif;font-size:25px;line-height:30px;color:var(--sand)}
.brand-dot{display:inline-block;width:12px;height:12px;border-radius:50%;background:var(--sand);margin-right:8px;vertical-align:middle}
.search{left:1000px;top:75px;width:113px;height:20px;border-radius:10px;background:var(--sand);font-size:12px;padding:3px 11px;color:var(--ink)}
.search-go{left:1120px;top:79px;font-size:12px;color:#5b5b5b}
.message{left:41px;top:172px;font-family:'Rye',serif;font-size:17px;color:var(--teal)}
.newsletter{left:39px;top:216px;font-family:'Rye',serif;font-size:17px;color:var(--ink)}
.email{left:39px;top:246px;width:114px;height:19px;border-radius:10px;background:var(--dark);color:var(--teal);font-size:12px;padding:2px 11px}
.email-go{left:159px;top:249px;font-size:12px;color:var(--teal)}
.side-title{font-family:'Rye',serif;font-size:13px;color:var(--ink)}
.side-list{list-style:none;font-size:10.5px;line-height:13px;margin-top:9px}
.categories{left:39px;top:302px}
.information{left:39px;top:566px}
.offer{left:39px;top:667px;width:169px;height:188px;background:linear-gradient(160deg,#9a8a78 0%,#7a95a8 45%,#5fa0c4 100%)}
.offer-title{left:0;width:169px;top:143px;text-align:center;font-family:'Rye',serif;font-size:17px;color:#fff}
.offer-sub{left:0;width:169px;top:166px;text-align:center;font-size:12.5px;color:#fff}
.hero{left:245px;top:153px;width:695px;height:278px;background:linear-gradient(120deg,#8a8f94 0%,#a9c2cf 35%,#7ec3e2 70%,#9bcfe6 100%)}
.hero-title{right:13px;top:10px;font-family:'Rye',serif;font-size:30px;color:#fff}
.dots{left:577px;top:454px;display:flex;gap:10px}
.dot{width:8px;height:8px;border-radius:50%;border:1.5px solid var(--dark)}
.dot.active{background:var(--dark)}
.featured{left:254px;top:505px;font-family:'Rye',serif;font-size:22px;color:var(--ink)}
.product-photo{left:245px;top:550px;width:130px;height:184px;background:linear-gradient(180deg,#6fd4ea 0%,#3c4148 45%,#2c2f33 100%)}
.product-name{left:245px;top:759px;width:160px;font-size:11.5px;line-height:14px;color:var(--ink);text-transform:uppercase}
.product-price{left:249px;top:811px;font-size:16px;color:var(--teal);font-weight:700}
.cart-title{left:981px;width:178px;top:157px;text-align:center;font-family:'Rye',serif;font-size:17px;color:var(--ink)}
.cart{left:981px;top:183px;width:178px;height:93px;background:var(--tan)}
.subtotal{left:9px;top:9px;width:161px;display:flex;justify-content:space-between;font-size:12px}
.cart-btn{left:29px;width:114px;height:19px;border-radius:10px;background:var(--cream);font-size:12px;text-align:center;line-height:19px}
.footer{left:0;top:878px;width:1200px;height:26px;background:var(--dark)}
</style>
</head>
<body>
<div class="abs topbar"></div>
<nav class="abs topnav"><span>MEN'S WESTERN WEAR</span><span>WOMEN'S WESTERN WEAR</span><span>NEW ARRIVALS!</span><span>BOOTS</span></nav>
<nav class="abs helpnav"><span>SIZING CHARTS</span><span>HELP</span></nav>
<svg class="abs account-icons" width="64" height="18" viewBox="0 0 64 18">
  <circle cx="7" cy="4.5" r="3.5" fill="#e0d6c0"/>
  <path d="M1 15c0-4 3-6 6-6s6 2 6 6z" fill="#e0d6c0"/>
  <path d="M15 10l2.5 2.5L20 10" stroke="#e0d6c0" stroke-width="1.6" fill="none"/>
  <path d="M27 2h3l3 9h10l2-7H32" stroke="#e0d6c0" stroke-width="2" fill="none"/>
  <circle cx="34" cy="15" r="1.6" fill="#e0d6c0"/><circle cx="42" cy="15" r="1.6" fill="#e0d6c0"/>
  <path d="M49 10l2.5 2.5L54 10" stroke="#e0d6c0" stroke-width="1.6" fill="none"/>
</svg>
<header class="abs header"></header>
<div class="abs brand"><span class="brand-dot"></span>Dusty Spur<br>Outfitters</div>
<div class="abs search">Search...</div>
<div class="abs search-go">GO!</div>

<aside>
  <div class="abs message">LEAVE US A MESSAGE!</div>
  <div class="abs newsletter">Join our Newsletter!</div>
  <div class="abs email">Email</div>
  <div class="abs email-go">GO!</div>
  <div class="abs categories">
    <div class="side-title">CATEGORIES</div>
    <ul class="side-list">
      <li>Men's Western Wear</li><li>Women's Western Wear</li><li>Boots</li><li>Accessories</li><li>Belts</li><li>Big and tall</li><li>Brand New Arrivals</li><li>CLEARANCE</li><li>Handbags</li><li>Jackets</li><li>Jeans</li><li>Leather</li><li>ON Sale</li><li>Pants</li><li>Short Sleeves</li><li>T-Shirts</li><li>Vests</li>
    </ul>
  </div>
  <div class="abs information">
    <div class="side-title">INFORMATION</div>
    <ul class="side-list">
      <li>About Us</li><li>Contact Us</li><li>Privacy Policy</li><li>Shipping and Returns</li><li>Sizing Charts</li>
    </ul>
  </div>
  <div class="abs offer" role="img" aria-label="Photo of a woman in a blue embroidered western shirt">
    <div class="abs offer-title">SPECIAL OFFER</div>
    <div class="abs offer-sub">25% Off Selected Products</div>
  </div>
</aside>

<main>
  <div class="abs hero" role="img" aria-label="Close-up of the back of a light blue western shirt with dark scroll embroidery">
    <div class="abs hero-title">NEW ARRIVALS</div>
  </div>
  <div class="abs dots"><span class="dot"></span><span class="dot active"></span></div>
  <h2 class="abs featured">FEATURED PRODUCTS</h2>
  <div class="abs product-photo" role="img" aria-label="Man wearing a dark embroidered western snap shirt on a turquoise background"></div>
  <div class="abs product-name">Prairie Ridge Men's Blue Thunder Western Snap Shirt</div>
  <div class="abs product-price">79.90 $</div>
</main>

<section>
  <div class="abs cart-title">SHOPPING CART</div>
  <div class="abs cart">
    <div class="abs subtotal"><span>Subtotal:</span><span>$ 0.00</span></div>
    <div class="abs cart-btn" style="top:32px">Update Cart</div>
    <div class="abs cart-btn" style="top:59px">Checkout</div>
  </div>
</section>

<footer class="abs footer"></footer>
</body>
</html>
```